brightwell - Property Management DL Card

I am after a savvy designer to cut through junk mail! so many real estate agents use flyers to promote themselves and their business and usually sales. We are a property management firm (residential) and we want to represent landlords that have existing investment properties and need a quality agent to represent them. Can you help?
DL size, will be printed and delivered to mailboxes. For a look at our website go to www.brightwellrs.com.au. Keep it simple and clutter free.
it is to be double sided - with one side to be simple and clear - just our website, logo and telephone number on the back.
attached is our logo and our telephone number is 1300 48 92 16
the above are 2 essential elements to be included + our email address: admin@brightwellrs.com.au
also attached are our transparent price list

Target Market(s)
property investors,
people that manage properties themselves
Industry/Entity Type
Property Management
- arial
Look and feel

```html
<!DOCTYPE html>
<html lang="en">
<head>
<meta charset="utf-8">
<title>brightwell – Property Management DL Card</title>
<link href="https://fonts.googleapis.com/css2?family=Open+Sans:wght@300;400;600;700&display=swap" rel="stylesheet">
<style>
  :root {
    --backdrop: #d9d9d9;
    --ink-black: #050505;
    --brand-red: #c4402a;
    --white: #ffffff;
    --soft-white: #e8e8e8;
    --divider: #e9b7ad;
  }
  * { margin: 0; padding: 0; box-sizing: border-box; }
  html, body {
    width: 1200px;
    height: 1200px;
    overflow: hidden;
    background: var(--backdrop);
    font-family: "Open Sans", Arial, sans-serif;
  }
  .canvas { position: relative; width: 1200px; height: 1200px; }

  .card { position: absolute; left: 119px; width: 1001px; height: 500px; overflow: hidden; }
  .card--front { top: 58px; }
  .card--back { top: 637px; background: var(--ink-black); }

  .hero-photo {
    position: absolute; left: 0; top: 0; width: 719px; height: 426px;
    background:
      linear-gradient(180deg, rgba(255,255,255,0) 0%, rgba(255,255,255,0) 72%, rgba(70,72,76,0.85) 100%),
      linear-gradient(90deg, #a9c4d2 0%, #7fb1c6 25%, #e4ebee 45%, #f2f4f5 70%, #dfe5e8 100%);
  }
  .brand-panel {
    position: absolute; left: 719px; top: 0; width: 282px; height: 426px;
    background: var(--ink-black);
  }
  .wordmark {
    font-weight: 300;
    color: var(--white);
    letter-spacing: 0.5px;
    line-height: 1;
  }
  .brand-panel .wordmark {
    position: absolute; left: 58px; top: 186px; font-size: 40px;
  }

  .feature-band {
    position: absolute; left: 0; top: 426px; width: 1001px; height: 74px;
    background: var(--brand-red);
    color: var(--white);
  }
  .feature-band__title {
    position: absolute; left: 31px; top: 19px;
    font-size: 25px; font-weight: 600; letter-spacing: 0.2px;
  }
  .feature-band__rule {
    position: absolute; left: 495px; top: 17px; width: 1px; height: 38px;
    background: var(--divider);
  }
  .feature-list {
    position: absolute; top: 16px; list-style: none;
    font-size: 16px; line-height: 21px;
  }
  .feature-list li::before { content: "\2022"; margin-right: 7px; }
  .feature-list--left { left: 524px; }
  .feature-list--right { left: 770px; }

  .card--back .wordmark {
    position: absolute; left: 53px; top: 50px; font-size: 42px;
  }
  .contact-block {
    position: absolute; left: 517px; top: 368px;
    border-left: 1px solid #8a8a8a;
    padding-left: 21px;
    color: var(--soft-white);
  }
  .contact-block__cta {
    font-size: 21px; font-weight: 700; color: var(--brand-red);
    line-height: 28px; letter-spacing: 0.2px;
  }
  .contact-block__cta span { margin-left: 14px; }
  .contact-block__line {
    font-size: 17px; line-height: 25px; letter-spacing: 0.6px;
  }
</style>
</head>
<body>
<div class="canvas">

  <section class="card card--front">
    <div class="hero-photo" role="img" aria-label="Bright modern apartment living room with white sofas and floor-to-ceiling windows overlooking the ocean"></div>
    <div class="brand-panel">
      <div class="wordmark">brightwell</div>
    </div>
    <div class="feature-band">
      <h1 class="feature-band__title">Property Management specialists</h1>
      <div class="feature-band__rule"></div>
      <ul class="feature-list feature-list--left">
        <li>Excellent communication</li>
        <li>Minimal vacancy</li>
      </ul>
      <ul class="feature-list feature-list--right">
        <li>No hidden extras</li>
        <li>The best rent return</li>
      </ul>
    </div>
  </section>

  <section class="card card--back">
    <div class="wordmark">brightwell</div>
    <div class="contact-block">
      <p class="contact-block__cta">CONTACT US TODAY!<span>1300 48 92 16</span></p>
      <p class="contact-block__line">PO Box B327, Sydney South NSW, 1240</p>
      <p class="contact-block__line">admin@brightwellrs.com.au</p>
    </div>
  </section>

</div>
</body>
</html>
```